Wordpress design for media production company

We are a small production company called Copper Lantern Films specializing in documentary and short film.

We are after a wordpress web site that is fun and engaging with a relaxed feel. We would like to be able to easily edit and maintain the website ourselves.

We would like:
* A title screen that has a photo taking up most of the screen.
* Contact details (inc. social media links) on a static bar at the bottom.
* An area for our previous work. Some thumbnails or icons that open up and embedded youtube or vimeo video.
* An area for "about us" which will have information on the company and links to separate profiles of 3 (initially) employees.
* A Blog.
* Somewhere to show what we are currently working on.
* Examples of other stuff we have done (ie. photography, poetry, audio, animation and VFX).

We already have a logo that can be animated. It would be very cool to have it as a "Loading" page while things load in the background.

The text needs to be fun but easy to read.

We already have a license for "Q Layout" which seems pretty cool and flexible, so if you wanted to use it then great but if not then that is fine too.

A couple of pages that we like are:
http://www.plumorchardworks.com/
http://dorianvelkot.com/
http://www.spinthegrove.com/

Please do not hesitate to contact me if you would like more information on anything.

Cheers

Gideon

Target Market(s)

Mainly Australian clients seeking media services
Broadcasting companies

Industry/Entity Type

It Company

Requirements
Nice to have
• I love the parallax look on http://www.plumorchardworks.com/

```html
<!DOCTYPE html>
<html lang="en">
<head>
<meta charset="utf-8">
<title>Copper Lantern Films</title>
<link href="https://fonts.googleapis.com/css2?family=Open+Sans:wght@400;600;700&display=swap" rel="stylesheet">
<style>
:root{
  --black:#000;
  --red:#b80000;
  --red-text:#c0100f;
  --white:#fff;
  --ink:#333;
  --muted:#555;
  --panel:#ebebeb;
  --panel-edge:#c9c9c9;
  --tag:#e2e2e2;
  --footer:#222;
  --footer-line:#3c3c3c;
  --footer-text:#ddd;
  --blue:#2f8fe4;
  --head:'Open Sans',Arial,sans-serif;
  --body:Arial,Helvetica,sans-serif;
}
*{box-sizing:border-box;margin:0;padding:0}
html,body{width:1200px;height:2804px;overflow:hidden}
body{position:relative;background:var(--white);font-family:var(--body);color:var(--ink)}
.abs{position:absolute}

/* header */
.site-header{left:0;top:0;width:1200px;height:191px;background:var(--black);color:var(--white)}
.brand{left:84px;top:22px;width:140px;text-align:center}
.brand-mark{display:block;width:100px;height:100px;margin:0 auto 10px;border-radius:50%;background:var(--white)}
.brand-name{font-family:var(--head);font-weight:700;font-size:17px;line-height:20px;color:var(--white)}
.call{right:96px;top:38px;text-align:right;font-family:var(--head)}
.call-label{font-size:19px;line-height:24px}
.call-number{font-size:25px;line-height:32px}
.call-icon{right:60px;top:50px}
.main-nav{top:132px;left:0;width:1200px;font-family:var(--head);font-size:16px;text-transform:uppercase}
.main-nav a{position:absolute;color:var(--white);text-decoration:none}

/* hero */
.hero{left:0;top:191px;width:1200px;height:435px;background:linear-gradient(180deg,#e9ecec 0%,#c9cfc8 35%,#6f7a5f 65%,#4d5537 100%)}
.hero-title{left:86px;top:361px;font-family:var(--head);font-size:35px;color:#111;letter-spacing:-.3px}
.hero-sub{left:88px;top:414px;font-family:var(--head);font-size:19px;color:var(--red-text)}
.dots{left:86px;top:589px;display:flex;gap:11px}
.dots span{width:17px;height:17px;border-radius:50%;background:rgba(255,255,255,.7)}

/* about */
.section-title{left:0;width:1200px;text-align:center;font-family:var(--head);font-size:29px;color:var(--red-text)}
.about-copy{left:88px;top:726px;width:1024px;text-align:center;font-size:14px;line-height:22px;color:var(--muted)}
.feature{width:280px;text-align:center}
.feature-icon{display:block;margin:0 auto;width:82px;height:82px;border-radius:50%;background:var(--red)}
.feature-title{margin-top:22px;font-size:24px;color:var(--red-text);font-family:var(--head)}
.feature-copy{margin-top:10px;font-size:14px;line-height:21px;color:var(--muted)}

/* latest works */
.work-card{top:1181px;width:321px;height:284px}
.work-thumb{position:relative;height:202px}
.play{position:absolute;left:50%;top:50%;width:58px;height:58px;margin:-29px 0 0 -29px;border-radius:50%;background:rgba(40,40,40,.55);border:2px solid rgba(255,255,255,.85)}
.work-band{height:82px;background:var(--red);color:var(--white);text-align:center}
.work-title{padding-top:14px;font-family:var(--head);font-size:22px;text-transform:uppercase}
.work-sub{margin-top:6px;font-size:13px}

/* filters */
.filters{top:1534px;left:0;width:1200px;height:38px}
.filter{position:absolute;top:0;height:38px;line-height:38px;background:var(--tag);text-align:center;font-family:var(--head);font-size:16px;color:#555;text-transform:uppercase}

/* gallery */
.gallery-card{width:321px;height:297px;border-bottom:5px solid var(--panel-edge);background:var(--panel)}
.gallery-thumb{height:198px}
.gallery-title{margin-top:26px;text-align:center;font-family:var(--head);font-size:17px;color:#555;text-transform:uppercase}
.gallery-sub{margin-top:8px;text-align:center;font-size:13px;color:#666}

/* footer */
.site-footer{left:0;top:2358px;width:1200px;height:446px;background:var(--footer);color:var(--footer-text)}
.footer-heading{font-family:var(--head);font-weight:600;font-size:20px;color:var(--white);text-transform:uppercase}
.blog-entry{left:90px;width:340px;font-size:13.5px;line-height:24px;color:var(--footer-text)}
.blog-entry .entry-icon{position:absolute;left:0;top:5px}
.blog-entry p{margin-left:28px}
.blog-entry em{display:block;margin-left:28px;font-size:12.5px}
.newsletter-copy{left:506px;top:2450px;width:260px;font-size:13.5px;line-height:24px}
.email-field{left:506px;top:2510px;width:246px;height:34px;background:var(--white);color:#777;font-size:13.5px;line-height:34px;padding-left:10px}
.subscribe{left:637px;top:2564px;width:115px;height:36px;background:var(--blue);color:var(--white);font-size:15px;line-height:36px;text-align:center;text-transform:uppercase}
.site-map{left:863px;top:2438px;font-size:13.5px;line-height:28.5px}
.site-map a{display:block;color:var(--footer-text);text-decoration:none}
.footer-rule{left:88px;top:2720px;width:1026px;height:1px;background:var(--footer-line)}
.copyright{left:90px;top:2748px;font-size:13.5px}
.social{left:913px;top:2743px;display:flex;gap:8px}
.social span{width:28px;height:28px;border-radius:50%;background:#7a7a7a}
</style>
</head>
<body>

<header class="site-header abs">
  <div class="brand abs">
    <span class="brand-mark"></span>
    <div class="brand-name">Copper Lantern Films</div>
  </div>
  <div class="call abs">
    <div class="call-label">Call today</div>
    <div class="call-number">+61 02 5550 1742</div>
  </div>
  <svg class="call-icon abs" width="26" height="36" viewBox="0 0 26 36" aria-hidden="true">
    <path d="M6 2 L12 2 L14 10 L10 13 Q12 22 18 26 L22 23 L26 29 L24 34 Q10 34 4 16 Q2 8 6 2Z" fill="#d00"/>
  </svg>
  <nav class="main-nav abs">
    <a style="left:548px">Home</a>
    <a style="left:652px">About us</a>
    <a style="left:785px">Our works</a>
    <a style="left:940px">Blog</a>
    <a style="left:1037px">Contact</a>
  </nav>
</header>

<section class="hero abs" role="img" aria-label="Hiker standing on a cliff top with arms wide over a misty forest valley"></section>
<h1 class="hero-title abs" style="font-weight:400">Duis autem vel eum iriure dolor in hendrerit</h1>
<p class="hero-sub abs">Typi non habent claritatem insitam; est usus legentis in iis qui facit</p>
<div class="dots abs"><span></span><span></span><span></span><span></span></div>

<h2 class="section-title abs" style="top:669px;font-weight:400">About us</h2>
<p class="about-copy abs">Vivamus sagittis lacus vel augue laoreet rutrum faucibus dolor auctor. Aenean lacinia bibendum nulla sed consectetur. Because we think it's time for a new excit e! Are you ready for an adventure to remember for a lifetime? Accusantium quaim, ultricies eget tempor id, aliquam eget nibh et. Maecen aliquains</p>

<div class="feature abs" style="left:142px;top:821px">
  <svg class="feature-icon" viewBox="0 0 82 82" aria-hidden="true"><circle cx="41" cy="41" r="41" fill="#b80000"/><circle cx="41" cy="41" r="14" fill="none" stroke="#fff" stroke-width="3" stroke-dasharray="5 3"/><circle cx="41" cy="41" r="6" fill="none" stroke="#fff" stroke-width="2.5"/></svg>
  <div class="feature-title">Services</div>
  <p class="feature-copy">Lorem ipsum dolor sit amet adipis msan. Morbi ut elit utipsum tristiqeua Pellentesque habitant morbi.</p>
</div>
<div class="feature abs" style="left:456px;top:821px">
  <svg class="feature-icon" viewBox="0 0 82 82" aria-hidden="true"><circle cx="41" cy="41" r="41" fill="#b80000"/><path d="M41 24 L57 32 L57 50 L41 58 L25 50 L25 32Z" fill="#fff"/><path d="M25 32 L41 40 L57 32 M41 40 L41 58" stroke="#b80000" stroke-width="2" fill="none"/></svg>
  <div class="feature-title">Who we are?</div>
  <p class="feature-copy">Lorem ipsum dolor sit amet adipis msan. Morbi ut elit utipsum tristiqeua Pellentesque habitant morbi.</p>
</div>
<div class="feature abs" style="left:778px;top:821px">
  <svg class="feature-icon" viewBox="0 0 82 82" aria-hidden="true"><circle cx="41" cy="41" r="41" fill="#b80000"/><circle cx="41" cy="36" r="13" fill="#fff"/><rect x="35" y="47" width="12" height="10" rx="2" fill="#fff"/></svg>
  <div class="feature-title">Free Updates</div>
  <p class="feature-copy">Lorem ipsum dolor sit amet adipis msan. Morbi ut elit utipsum tristiqeua Pellentesque habitant morbi.</p>
</div>

<h2 class="section-title abs" style="top:1093px;font-weight:400">Latest Works</h2>

<article class="work-card abs" style="left:86px">
  <div class="work-thumb" role="img" aria-label="Dancer leaping with a blue fabric against the sky" style="background:linear-gradient(160deg,#2f7fd0,#8cc4ee)"><span class="play"></span></div>
  <div class="work-band"><div class="work-title">Project #1</div><div class="work-sub">Proin gravida nibh vel velit</div></div>
</article>
<article class="work-card abs" style="left:437px">
  <div class="work-thumb" role="img" aria-label="Women walking together in a park" style="background:linear-gradient(160deg,#6c7a2c,#b9a55a)"><span class="play"></span></div>
  <div class="work-band"><div class="work-title">Project #2</div><div class="work-sub">Proin gravida nibh vel velit</div></div>
</article>
<article class="work-card abs" style="left:792px">
  <div class="work-thumb" role="img" aria-label="Two older women jogging outdoors" style="background:linear-gradient(160deg,#7aa03c,#d8e6a8)"><span class="play"></span></div>
  <div class="work-band"><div class="work-title">Project #2</div><div class="work-sub">Proin gravida nibh vel velit</div></div>
</article>

<div class="filters abs">
  <span class="filter" style="left:321px;width:165px">Photography</span>
  <span class="filter" style="left:506px;width:99px">Poetry</span>
  <span class="filter" style="left:628px;width:88px">Audio</span>
  <span class="filter" style="left:744px;width:131px">Animation</span>
</div>

<article class="gallery-card abs" style="left:86px;top:1626px">
  <div class="gallery-thumb" role="img" aria-label="Dumbbells resting on a blue floor" style="background:linear-gradient(180deg,#1f3f5e,#6d7c86)"></div>
  <div class="gallery-title">Claritas est etiam processus</div><div class="gallery-sub">Lorem ipsum reprehenderit minim</div>
</article>
<article class="gallery-card abs" style="left:439px;top:1626px">
  <div class="gallery-thumb" role="img" aria-label="Family playing in the sea surf at sunset" style="background:linear-gradient(180deg,#c9ad86,#6f7f86)"></div>
  <div class="gallery-title">Claritas est etiam processus</div><div class="gallery-sub">Lorem ipsum reprehenderit minim</div>
</article>
<article class="gallery-card abs" style="left:794px;top:1626px">
  <div class="gallery-thumb" role="img" aria-label="Silhouette of a person jumping against a bright sky" style="background:linear-gradient(180deg,#1a7fd6,#bfe2fb)"></div>
  <div class="gallery-title">Claritas est etiam processus</div><div class="gallery-sub">Lorem ipsum reprehenderit minim</div>
</article>
<article class="gallery-card abs" style="left:86px;top:1987px">
  <div class="gallery-thumb" role="img" aria-label="Gardener in an apron among flowers" style="background:linear-gradient(160deg,#4d6a2a,#c77a78)"></div>
  <div class="gallery-title">Claritas est etiam processus</div><div class="gallery-sub">Lorem ipsum reprehenderit minim</div>
</article>
<article class="gallery-card abs" style="left:439px;top:1987px">
  <div class="gallery-thumb" role="img" aria-label="Scuba divers underwater giving an okay sign" style="background:linear-gradient(160deg,#0d3f66,#2c8fc0)"></div>
  <div class="gallery-title">Claritas est etiam processus</div><div class="gallery-sub">Lorem ipsum reprehenderit minim</div>
</article>
<article class="gallery-card abs" style="left:794px;top:1987px">
  <div class="gallery-thumb" role="img" aria-label="Group raising arms in a sunlit meadow" style="background:linear-gradient(180deg,#f4ef9a,#a7b63a)"></div>
  <div class="gallery-title">Claritas est etiam processus</div><div class="gallery-sub">Lorem ipsum reprehenderit minim</div>
</article>

<footer class="site-footer abs"></footer>
<h3 class="footer-heading abs" style="left:90px;top:2390px">Blog Entry</h3>
<h3 class="footer-heading abs" style="left:505px;top:2390px">Newsletter Signup</h3>
<h3 class="footer-heading abs" style="left:862px;top:2390px">Site Map</h3>

<div class="blog-entry abs" style="top:2446px">
  <svg class="entry-icon" width="17" height="17" viewBox="0 0 17 17" aria-hidden="true"><rect width="17" height="17" rx="4" fill="#ddd"/><rect x="4" y="5" width="9" height="2" fill="#222"/><rect x="4" y="10" width="7" height="2" fill="#222"/></svg>
  <p>Mara : Vivamus sagittis lacus vel augue laor mfaucibus dolor auctor lorem Aenean.</p><em>Posted on March 14, 2013</em>
</div>
<div class="blog-entry abs" style="top:2530px">
  <svg class="entry-icon" width="17" height="17" viewBox="0 0 17 17" aria-hidden="true"><rect width="17" height="17" rx="4" fill="#ddd"/><rect x="4" y="5" width="9" height="2" fill="#222"/><rect x="4" y="10" width="7" height="2" fill="#222"/></svg>
  <p>Mara : Vivamus sagittis lacus vel augue laor mfaucibus dolor auctor lorem Aenean.</p><em>Posted on March 14, 2013</em>
</div>
<div class="blog-entry abs" style="top:2614px">
  <svg class="entry-icon" width="17" height="17" viewBox="0 0 17 17" aria-hidden="true"><rect width="17" height="17" rx="4" fill="#ddd"/><rect x="4" y="5" width="9" height="2" fill="#222"/><rect x="4" y="10" width="7" height="2" fill="#222"/></svg>
  <p>Mara : Vivamus sagittis lacus vel augue laor mfaucibus dolor auctor lorem Aenean.</p><em>Posted on March 14, 2013</em>
</div>

<p class="newsletter-copy abs">Stay in touch with us by signing up for our quarterly&nbsp; newsletter!</p>
<div class="email-field abs">Enter Email Id</div>
<div class="subscribe abs">Subscribe</div>

<nav class="site-map abs">
  <a>Home</a><a>Our Works</a><a>About Us</a><a>Blog</a><a>&nbsp;Contact</a>
</nav>

<div class="footer-rule abs"></div>
<p class="copyright abs">© 2013 Copyrights. All Rights Reserved.</p>
<div class="social abs" aria-label="Social links"><span></span><span></span><span></span><span></span></div>

</body>
</html>
```